Modern Business Card

Modern professional business card with more than just logo and demographic info. Something memorable.

We are a trendy/modern chiropractic group with an emphasis on neurology, hence the minimalist-type brain logo. We want to convey that modern and technical aspect with professionalism and the elite nature of our practice environment.

```html
<!DOCTYPE html>
<html lang="en">
<head>
<meta charset="utf-8">
<title>Kestrel Spine – Business Card</title>
<link rel="stylesheet" href="https://fonts.googleapis.com/css2?family=Open+Sans:wght@400;600&display=swap">
<style>
  :root {
    --canvas: #d2d6d7;
    --card-white: #f7f7f6;
    --brand-blue: #2f6db5;
    --ink: #1c1c1c;
    --ink-soft: #3a3a3a;
    --white: #ffffff;
  }
  * { box-sizing: border-box; margin: 0; padding: 0; }
  html, body {
    width: 1200px; height: 1200px; overflow: hidden;
    background: var(--canvas);
    font-family: "Open Sans", sans-serif;
  }
  .sheet {
    position: relative; width: 1200px; height: 1200px;
    display: flex; flex-direction: column; align-items: center; justify-content: center; gap: 60px;
  }
  .card {
    position: relative; width: 620px; height: 354px;
    box-shadow: 0 10px 30px rgba(0,0,0,0.12);
  }
  .card--front { background: var(--card-white); }
  .card--back {
    background: var(--brand-blue);
    display: flex; align-items: center; justify-content: center; gap: 18px;
  }

  .brand { display: flex; align-items: center; gap: 14px; }
  .brand__dot { width: 30px; height: 30px; border-radius: 50%; background: var(--brand-blue); flex: none; }
  .brand__name {
    font-weight: 600; font-size: 34px; letter-spacing: 0.08em; line-height: 1;
    color: var(--ink); text-transform: uppercase;
  }
  .card--front .brand { position: absolute; top: 66px; right: 40px; }
  .card--back .brand__dot { background: var(--white); width: 40px; height: 40px; }
  .card--back .brand__name { color: var(--white); font-size: 46px; }

  .person { position: absolute; left: 40px; top: 62px; }
  .person__name { color: var(--brand-blue); font-weight: 600; font-size: 28px; line-height: 1.1; }
  .person__role { color: var(--ink-soft); font-size: 14px; margin-top: 2px; }

  .contacts {
    position: absolute; left: 40px; top: 170px;
    list-style: none; display: flex; flex-direction: column; gap: 9px;
  }
  .contacts li { display: flex; align-items: center; gap: 12px; font-size: 15px; color: var(--ink); }
  .contacts svg { width: 18px; height: 18px; fill: var(--brand-blue); flex: none; }
  .contacts .accent { color: var(--brand-blue); }

  .divider {
    position: absolute; left: 330px; top: 250px; width: 1px; height: 52px;
    background: var(--brand-blue); opacity: 0.6;
  }
  .address { position: absolute; left: 350px; top: 250px; font-size: 15px; color: var(--ink); line-height: 1.7; }
  .address__line { display: flex; align-items: center; gap: 8px; }
  .address svg { width: 14px; height: 18px; fill: var(--brand-blue); }
  .address__indent { padding-left: 0; }
</style>
</head>
<body>
<main class="sheet">

  <section class="card card--front" aria-label="Business card front">
    <div class="person">
      <h1 class="person__name">Daniel Reyes</h1>
      <p class="person__role">neurologist</p>
    </div>

    <div class="brand">
      <span class="brand__dot"></span>
      <span class="brand__name">Kestrel Spine</span>
    </div>

    <ul class="contacts">
      <li>
        <svg viewBox="0 0 24 24" aria-hidden="true"><path d="M6.6 10.8a15.1 15.1 0 0 0 6.6 6.6l2.2-2.2c.3-.3.7-.4 1-.2 1.1.4 2.3.6 3.6.6.6 0 1 .4 1 1V20c0 .6-.4 1-1 1A17 17 0 0 1 3 4c0-.6.4-1 1-1h3.5c.6 0 1 .4 1 1 0 1.3.2 2.5.6 3.6.1.3 0 .7-.2 1z"/></svg>
        <span>1-555-014-2290</span>
      </li>
      <li>
        <svg viewBox="0 0 24 24" aria-hidden="true"><path d="M12 2a10 10 0 1 0 0 20 10 10 0 0 0 0-20zm6.9 6h-2.9a15.6 15.6 0 0 0-1.4-3.6A8 8 0 0 1 18.9 8zM12 4c.8 1.2 1.5 2.5 1.9 4h-3.8c.4-1.4 1.1-2.8 1.9-4zM4.3 14a8 8 0 0 1 0-4h3.4a16.5 16.5 0 0 0 0 4zm.8 2h2.9c.3 1.3.8 2.5 1.4 3.6A8 8 0 0 1 5.1 16zM8 8H5.1a8 8 0 0 1 4.3-3.6C8.8 5.5 8.3 6.7 8 8zm4 12c-.8-1.2-1.5-2.5-1.9-4h3.8c-.4 1.4-1.1 2.8-1.9 4zm2.3-6H9.7a14.7 14.7 0 0 1 0-4h4.6a14.7 14.7 0 0 1 0 4zm.3 5.6c.6-1.1 1.1-2.3 1.4-3.6h2.9a8 8 0 0 1-4.3 3.6zm1.7-5.6a16.5 16.5 0 0 0 0-4h3.4a8 8 0 0 1 0 4z"/></svg>
        <span>daniel@<span class="accent">kestrelspine</span>.com</span>
      </li>
      <li>
        <svg viewBox="0 0 24 24" aria-hidden="true"><path d="M2 5h20v14H2zm2 2v.5l8 5 8-5V7zm0 2.8V17h16V9.8l-8 5z"/></svg>
        <span>www.<span class="accent">kestrelspine</span>.com</span>
      </li>
    </ul>

    <div class="divider"></div>
    <div class="address">
      <div class="address__line">
        <svg viewBox="0 0 14 18" aria-hidden="true"><path d="M7 0a7 7 0 0 0-7 7c0 5 7 11 7 11s7-6 7-11a7 7 0 0 0-7-7zm0 9.5A2.5 2.5 0 1 1 7 4.5a2.5 2.5 0 0 1 0 5z"/></svg>
        <span>Dummy city</span>
      </div>
      <div class="address__indent">Dummy Country Land</div>
    </div>
  </section>

  <section class="card card--back" aria-label="Business card back">
    <div class="brand">
      <span class="brand__dot"></span>
      <span class="brand__name">Kestrel Spine</span>
    </div>
  </section>

</main>
</body>
</html>
```